Business Card - high end, modern health care

Hey designers!

We need a double sided business card for the boutique, cutting edge physical therapy rehabilitation centre in Sydney's Northern Beaches.

With the most qualified physios in the area The Harbourview Motion Clinic does what other physiotherapy practices do not, we take our time with our patients giving them longer appointments, better physios and therefor faster results!

We guarantee that the service people receive at THMC will be unparalleled.

Hence we need a business card to reflect our modern, boutique, high end service. The final design needs to reflect that we are in a class of our own yet with the feel of beachside retreat.

Below I have attached our logo in both blue on white and white on blue. The exact colour is;
and the font that we have used in our logo is Tex Gyre Aventador.

I like the idea of the blue as the main colour as it is more eye catching and our signage onto the main road will be in this blue and in the interest of consistency across marketing the blue needs to be a part of the design. However I would appreciate a few designs onto a wooden background as this is a visual theme within the fitout of the practice.

The design needs to be of standard size (91x55mm).

Target Market(s)

We target people who have an end outcome in mind and those who have had poor experiences with other providers and ensure that everyone gets the care that they deserve with a premium service that is tailored to the individuals circumstances. As a premium service, the target market is highly educated, business and tech savvy with the additional target market of elderly people who have self funded their retirement and see value in paying for the best ongoing rehabilitation to maintain independence.

Industry/Entity Type

Physical Therapy

Contact Information for Business Card

Name, designation( Titled Musculoskeletal Physiotherapist... there will also be those in the company that have multiple designations ie 5 or 6 words long), phone number, email, facebook, instagram, address

Font styles to use
Sans Serif

Colors

Designer to choose colors to be used in the design.

Requirements
Must have
• Front - The logo as large as possible, blue or wooden theme, and all of the important details.
• Back - A blank space/lines on which to write appointment times (no "Appointment, date, time" etc.)
Nice to have
• facebook url
• logos for facebook and instagram
• Mini logos for the phone and email?

```html
<!DOCTYPE html>
<html lang="en">
<head>
<meta charset="utf-8">
<title>The Harbourview Motion Clinic – Business Card</title>
<link href="https://fonts.googleapis.com/css2?family=Lato:wght@400;700&display=swap" rel="stylesheet">
<style>
  :root {
    --backdrop: #8c532e;
    --kraft-light: #d9b385;
    --kraft-mid: #c59a67;
    --kraft-dark: #b4844f;
    --ink: #111111;
    --rule: #6e4f25;
    --paper: #f6f6f6;
  }
  * { margin: 0; padding: 0; box-sizing: border-box; }
  html, body { width: 1200px; height: 900px; overflow: hidden; }
  body {
    position: relative;
    background: var(--backdrop);
    font-family: "Lato", sans-serif;
    color: var(--ink);
  }
  .card {
    position: absolute;
    width: 556px;
    height: 343px;
    background: radial-gradient(ellipse at 30% 0%, var(--kraft-light) 0%, var(--kraft-mid) 50%, var(--kraft-dark) 100%);
    box-shadow: 3px 4px 6px rgba(0,0,0,0.45);
    overflow: hidden;
  }
  .card--front { left: 330px; top: 90px; }
  .card--back { left: 331px; top: 470px; width: 557px; }

  .front-mark {
    position: absolute;
    left: 52px; top: 110px;
    width: 170px;
    font-weight: 700;
    font-size: 24px;
    line-height: 1.15;
    text-transform: uppercase;
    text-align: center;
  }
  .front-divider {
    position: absolute;
    left: 254px; top: 90px;
    width: 1.5px; height: 153px;
    background: var(--rule);
  }
  .contact { position: absolute; left: 279px; top: 92px; }
  .contact__name { font-weight: 700; font-size: 20px; line-height: 24px; text-transform: uppercase; }
  .contact__role { font-size: 15px; line-height: 18px; }
  .contact__list { list-style: none; font-size: 15px; }
  .contact__list--direct { margin-top: 17px; }
  .contact__list--social { margin-top: 13px; }
  .contact__list li { display: flex; align-items: center; height: 20.5px; }
  .contact__icon { width: 17px; height: 17px; margin-right: 5px; flex: none; }

  .back-mark {
    position: absolute;
    left: 80px; top: 108px;
    display: flex; align-items: center;
  }
  .back-mark__dot {
    width: 68px; height: 68px; border-radius: 50%;
    background: var(--ink); margin-right: 10px;
  }
  .back-mark__name {
    font-weight: 700; font-size: 29px; line-height: 32px;
    text-transform: uppercase; letter-spacing: 1px;
  }
  .appointment-strip {
    position: absolute; left: 0; bottom: 0;
    width: 100%; height: 79px;
    background: var(--paper);
  }
  .appointment-strip__line {
    position: absolute; left: 102px; top: 32px;
    font-weight: 700; font-size: 13px; letter-spacing: 0.2px;
    display: flex; align-items: flex-end;
  }
  .blank { display: inline-block; border-bottom: 1px solid var(--ink); height: 12px; }
  .blank--date { width: 136px; }
  .blank--time { width: 138px; }
</style>
</head>
<body>

<section class="card card--front">
  <div class="front-mark">The Harbourview Motion Clinic</div>
  <div class="front-divider"></div>
  <div class="contact">
    <p class="contact__name">Marcus Ellery</p>
    <p class="contact__role">Managing Director</p>
    <ul class="contact__list contact__list--direct">
      <li>
        <svg class="contact__icon" viewBox="0 0 20 20"><circle cx="10" cy="10" r="8.8" fill="none" stroke="#111" stroke-width="1.6"/><path d="M6.5 5.5l2 0 1 2.5-1.3 1c.6 1.3 1.5 2.2 2.8 2.8l1-1.3 2.5 1v2c-4.5.3-8.3-3.5-8-8z" fill="#111"/></svg>
        020 5550 1472
      </li>
      <li>
        <svg class="contact__icon" viewBox="0 0 20 20"><circle cx="10" cy="10" r="8.8" fill="none" stroke="#111" stroke-width="1.6"/><rect x="5.5" y="7" width="9" height="6.5" fill="#111"/><path d="M5.8 7.3L10 10.5l4.2-3.2" fill="none" stroke="#c59a67" stroke-width="0.9"/></svg>
        hello@harbourviewmotion.com
      </li>
    </ul>
    <ul class="contact__list contact__list--social">
      <li>
        <svg class="contact__icon" viewBox="0 0 20 20"><circle cx="10" cy="10" r="9.5" fill="#111"/></svg>
        /harbourviewmotionclinic
      </li>
      <li>
        <svg class="contact__icon" viewBox="0 0 20 20"><circle cx="10" cy="10" r="9.5" fill="#111"/></svg>
        @harbourviewmotionclinic
      </li>
    </ul>
  </div>
</section>

<section class="card card--back">
  <div class="back-mark">
    <div class="back-mark__dot"></div>
    <div class="back-mark__name">The Harbourview<br>Motion Clinic</div>
  </div>
  <div class="appointment-strip">
    <p class="appointment-strip__line">DATE<span class="blank blank--date"></span>TIME<span class="blank blank--time"></span></p>
  </div>
</section>

</body>
</html>
```